Client website

Our designer we were working with had some personal things come up and was unable to finish the design for the site.

We have a .psd file started, and will be attaching it to the project.
Updates

Reason: I still want to polish the designs with the current designer and allow more designers the opportunity to participate.

Reason: I'm extending the deadline for another day to give everyone enough time for the final changes our client wants.

I'm trying to extend the deadline so we can get one last set of comps in for my client.  Could everyone message me and let me know how much time they need to do the final tweaks?

Reason: Hey everyone.  I've been sick the last 3 days and I haven't been able to provide feedback on designs.  I'm extending just a few more days so I can catch up here.  Thanks everyone for your patience.

Target Market(s)

Adults in United States aged 25 to 60 that handle the household budgets and maintenance.

Requirements
Must have
• 1) We need 2 pages. 1 page for flood restoration, 1 page for carpet cleaning

2) The 1-800-# must be the focal point of the website for both pages. People are mostly looking to contact someone ASAP to get them out to their house when flooding occurs.

3) We''re going to have a slide show area to high-light different sub-services offered for each page.

4) We really want a chatterbook / plinker feed area. We''re going to use chatterbook for special offers, and plinker for weather updates. The chatterbook feed is going to be on the carpet cleaning page. The plinker feed is going to be on the flood page.

5) We want an SEO text sections near the bottom.

6) The very bottom will link to the privacy policy and user agreement as well as company name and copyright details.

We really want to stick to the say "theme" that our first designer started with.
Nice to have
• I'm not a designer, so if you think something looks better somewhere, or something can be eliminated, or something can be enhanced, but all means, let us know.

```html
<!DOCTYPE html>
<html lang="en">
<head>
<meta charset="utf-8">
<title>Aqua-Crest — Water &amp; Fire Damage Restoration</title>
<link rel="stylesheet" href="https://fonts.googleapis.com/css2?family=Open+Sans:wght@400;600;700&family=Arimo:wght@400;700&display=swap">
<style>
:root{
  --page-bg:#3b3a2f;
  --page-bg-dark:#2f2e25;
  --carpet-light:#f0d3a6;
  --carpet-mid:#dcae72;
  --carpet-deep:#c98f4d;
  --tan:#c8945a;
  --tan-light:#d9a96c;
  --nav-blue:#0b5aa2;
  --nav-blue-dark:#064179;
  --nav-active:#f3a64a;
  --brown-text:#4a2c0c;
  --feed-bg:#a98043;
  --feed-border:#7a5526;
  --link-orange:#f7b25c;
  --green:#109a23;
  --green-dark:#0b7a1a;
  --tab-tan:#d99c55;
  --white:#ffffff;
  --footer-text:#e6e3d6;
  --footer-rule:#55544a;
}
*{box-sizing:border-box;margin:0;padding:0}
html,body{width:1200px;height:1138px;overflow:hidden}
body{
  background:var(--page-bg);
  background-image:radial-gradient(circle at 50% 30%,#45443a 0,var(--page-bg) 60%,var(--page-bg-dark) 100%);
  font-family:"Open Sans",Arial,sans-serif;
  position:relative;
}
.site{position:absolute;left:113px;top:23px;width:975px;height:897px;border-radius:8px;overflow:hidden;
  background:linear-gradient(180deg,var(--carpet-mid) 0,var(--carpet-mid) 300px,var(--tan) 560px,var(--tan-light) 897px);
  box-shadow:0 0 18px rgba(0,0,0,.45)}
.header{position:absolute;left:0;top:0;width:975px;height:241px;
  background:radial-gradient(ellipse at 20% 40%,#fbf0dc 0,var(--carpet-light) 35%,var(--carpet-mid) 75%,var(--carpet-deep) 100%)}
.brand{position:absolute;left:35px;top:40px;display:flex;align-items:center;gap:14px}
.brand-mark{width:44px;height:44px;border-radius:50%;background:#1a8fd6}
.brand-name{font-family:"Arimo",Arial,sans-serif;font-weight:700;font-size:40px;color:#1a8fd6;letter-spacing:1px}
.brand-tag{position:absolute;left:45px;top:212px;font-family:"Arimo",Arial,sans-serif;font-size:14px;color:#1a6fb8;letter-spacing:1px;font-variant:small-caps}
.call{position:absolute;left:587px;top:77px;width:326px;height:68px;background:rgba(255,240,215,.45);border-radius:4px;padding:4px 14px;color:var(--brown-text);font-family:"Arimo",Arial,sans-serif;font-weight:700;line-height:1}
.call small{display:block;font-size:23px}
.call strong{display:block;font-size:38px;margin-top:2px}
.nav{position:absolute;left:0;top:241px;width:975px;height:46px;background:linear-gradient(180deg,var(--nav-blue),var(--nav-blue-dark));display:flex;align-items:center;padding-left:54px}
.nav a{color:var(--white);font-weight:700;font-size:16px;text-decoration:none;padding:0 22px;border-left:1px solid rgba(255,255,255,.6);line-height:12px}
.nav a:first-child{border-left:0;padding-left:0;color:var(--nav-active)}
.slider{position:absolute;left:20px;top:306px;width:935px;height:224px;background:var(--white);box-shadow:0 2px 4px rgba(0,0,0,.25)}
.slide-photo{position:absolute;left:5px;top:5px;width:778px;height:214px;
  background:linear-gradient(90deg,#d9d6cc 0,#b8b4a8 30%,#8e8c84 48%,#7f7d76 100%)}
.slide-copy{position:absolute;left:380px;top:44px;width:390px;color:var(--white);font-family:Tahoma,"Open Sans",sans-serif;font-size:10.5px;line-height:13px}
.slide-copy h2{font-family:"Arimo",Arial,sans-serif;font-size:25px;font-weight:700;margin-bottom:6px}
.btn{display:inline-block;margin-top:20px;background:linear-gradient(180deg,#22b531,var(--green-dark));color:var(--white);font-weight:700;font-size:11px;padding:4px 10px;border:1px solid #0a5e14}
.tabs{position:absolute;left:787px;top:5px;width:143px}
.tabs li{list-style:none;height:43px;line-height:43px;padding-left:17px;color:var(--white);font-weight:700;font-size:11px;background:linear-gradient(180deg,#e0a862,#cf8f47);border-bottom:1px solid #f0c68c}
.tabs li.active{background:var(--green);position:relative}
.tabs li.active::before{content:"";position:absolute;left:-12px;top:0;border-top:21px solid transparent;border-bottom:22px solid transparent;border-right:12px solid var(--green)}
.feed-title{position:absolute;left:36px;top:555px;display:flex;align-items:center;gap:14px}
.feed-mark{width:110px;height:70px;background:#2c5d9e;border-radius:8px;transform:skewX(-8deg)}
.feed-title h3{font-family:"Arimo",Arial,sans-serif;font-size:23px;color:var(--white);font-weight:700;margin-top:12px}
.feed{position:absolute;left:19px;top:608px;width:936px;height:270px;background:var(--feed-bg);border:1px solid var(--feed-border);border-radius:6px;padding:40px 10px 0 11px;color:var(--white);font-family:Tahoma,"Open Sans",sans-serif;font-size:10.5px;line-height:14px}
.post{margin-bottom:16px}
.post:nth-child(2){margin-top:26px}
.meta{margin-top:8px;font-weight:700;display:flex;align-items:center;gap:9px}
.meta .user{color:var(--link-orange)}
.like{display:inline-block;border:1px solid #9aa9c9;background:#eef1f7;color:#3b5998;font-weight:400;border-radius:3px;padding:1px 5px;font-size:10px}
.footer{position:absolute;left:133px;top:937px;width:935px;display:flex}
.footer-col{flex:1;border-left:1px solid var(--footer-rule);padding:10px 0 0 14px;height:120px}
.footer-col:first-child{border-left:0}
.footer-col h4{color:var(--white);font-size:11px;font-weight:700;margin-bottom:18px}
.footer-col li{list-style:none;color:var(--footer-text);font-size:10.5px;line-height:18px;padding-left:12px;position:relative}
.footer-col li::before{content:"›";position:absolute;left:0;color:#999}
.legal{position:absolute;left:133px;top:1078px;width:935px;border-top:1px solid var(--footer-rule);text-align:center;padding-top:9px;color:var(--white);font-size:10px}
</style>
</head>
<body>
<div class="site">
  <header class="header">
    <div class="brand"><span class="brand-mark"></span><span class="brand-name">AQUA-CREST</span></div>
    <div class="brand-tag">Water &amp; Fire Damage Restoration</div>
    <div class="call"><small>CALL US</small><strong>1-800-555-0199</strong></div>
  </header>
  <nav class="nav">
    <a href="#">HOME</a><a href="#">ABOUT</a><a href="#">SERVICES</a><a href="#">FAQ</a><a href="#">CONTACT</a>
  </nav>
  <section class="slider">
    <div class="slide-photo" role="img" aria-label="Technician cleaning a carpet with a hose-fed extraction wand"></div>
    <div class="slide-copy">
      <h2>Sub-Service Heading</h2>
      <p><b>Lorem ipsum dolor sit amet, consectetur adipiscing elit. Quisque a rutrum massa.</b> Nullam pellentesque lobortis mi, iaculis pretium nisi semper vel. Donec vestibulum luctus diam id sodales. Duis semper dapibus eros, non fermentum ante tempor a. Integer scelerisque placerat mi sit amet scelerisque.</p>
      <span class="btn">Know more</span>
    </div>
    <ul class="tabs">
      <li class="active">Sub-Service 1</li><li>Sub-Service 2</li><li>Sub-Service 3</li><li>Sub-Service 4</li><li>Sub-Service 5</li>
    </ul>
  </section>
  <div class="feed-title"><span class="feed-mark"></span><h3>Find us on Chatterbook</h3></div>
  <section class="feed">
    <article class="post">
      <p>Lorem ipsum dolor sit amet, consectetur adipiscing elit. Sed quis ante felis. Donec porta arcu vehicula purus hendrerit interdum. Suspendisse lacus magna ullamcorper ut aliquet rutrum consectetur adipiscing elit. Sed quis ante felis. Donec porta arcu vehicula purus hendrerit interdum. Suspendisse lacus magna ullamcorper ut aliquet rutrum</p>
      <div class="meta">Posted by: <span class="user">username details</span> | 2 hrs ago | <span class="like">Like</span></div>
    </article>
    <article class="post">
      <p>Curabitur laoreet, elit in tincidunt condimentum, massa tortor adipiscing nisl, non condimentum orci nunc quis diam. Curabitur sed arcu ut ipsum tempor molestie sed eget ipsum. Lorem ipsum dolor sit amet, consectetur adipiscing elit. Sed quis ante felis. Donec porta arcu vehicula purus hendrerit interdum. Suspendisse lacus magna ullamcorper ut aliquet rutrum</p>
      <div class="meta">Posted by: <span class="user">username details</span> | 2 hrs ago | <span class="like">Like</span></div>
    </article>
    <article class="post">
      <p>Vivamus tempor feugiat felis nec fringilla. Aenean condimentum nunc ut felis pellentesque in aliquet orci pharetra. Duis pharetra pharetra est vel bibendum. Lorem ipsum dolor sit amet, consectetur adipiscing elit. Sed quis ante felis. Donec porta arcu vehicula purus hendrerit interdum. Suspendisse lacus magna ullamcorper ut aliquet rutrum</p>
      <div class="meta">Posted by: <span class="user">username details</span> | 2 hrs ago | <span class="like">Like</span></div>
    </article>
  </section>
</div>
<footer class="footer">
  <div class="footer-col"><h4>Home</h4><ul><li>Lorem ipsum dolor sit amet</li><li>Lorem ipsum dolor</li><li>Lorem ipsum dolor sit amet</li><li>Lorem ipsum</li></ul></div>
  <div class="footer-col"><h4>About</h4><ul><li>Lorem ipsum dolor sit amet</li><li>Lorem ipsum</li><li>Lorem ipsum dolor</li><li>Lorem ipsum dolor sit</li></ul></div>
  <div class="footer-col"><h4>Services</h4><ul><li>Lorem ipsum</li><li>Lorem ipsum dolor sit amet</li><li>Lorem ipsum dolor</li><li>Lorem ipsum</li></ul></div>
  <div class="footer-col"><h4>Faq</h4><ul><li>Lorem ipsum dolor sit</li><li>Lorem ipsum</li><li>Lorem ipsum dolor sit</li><li>Lorem ipsum dolor sit amet</li></ul></div>
  <div class="footer-col"><h4>Contact</h4><ul><li>Lorem ipsum dolor sit</li><li>Lorem ipsum dolor</li><li>Lorem ipsum dolor sit amet</li><li>Lorem ipsum</li></ul></div>
</footer>
<div class="legal">© 2011 Aqua-Crest. All rights reserved &nbsp;. Terms &amp; Conditions &nbsp;. Privacy Policy</div>
</body>
</html>
```